Tarn Workforce Tri Fold Brochure

My company is a recruiting/staffing firm. I need a design that is going to be professional, bright, young, hip and fun. Pictures are key! We want people working in an office, packaging, food production and/or light industrial environment. Must embrace DIVERSITY. Please use the 4 primary colors from the Tarn Logo to accent the piece, but not too busy. I am including the content that I would like to be included in the trifold as well as a sample of a trifold I have used in the past in addition to a couple of logos. My website is www.TarnWorkforce-example.com for look and feel.

Target Market(s)

Logistics, Distribution and Manufacturing companies

Industry/Entity Type

Staffing

Requirements
Must have
• Clean, colorful, eye catching, great pictures and graphics. Photo's of diverse people working, in a office, or production setting.
Nice to have
• Must be professional
Should not have
• Not too busy.

```html
<!DOCTYPE html>
<html lang="en">
<head>
<meta charset="utf-8">
<title>Tarn Workforce – Tri Fold Brochure</title>
<link href="https://fonts.googleapis.com/css2?family=Oswald:wght@500;600;700&family=Open+Sans:ital,wght@0,400;0,600;0,700;1,400&display=swap" rel="stylesheet">
<style>
:root{
  --navy:#2d2a78;
  --navy-deep:#221f63;
  --gold:#c9a23a;
  --red:#d7262b;
  --green:#2f9a44;
  --yellow:#f1bf12;
  --blue:#2b4ba2;
  --ink:#3b3b48;
  --paper:#ffffff;
  --stage:#ebe8e3;
}
*{box-sizing:border-box;margin:0;padding:0}
html,body{width:1200px;height:2400px;overflow:hidden}
body{background:var(--stage);font-family:"Open Sans",Arial,sans-serif;color:var(--ink);position:relative}
.spread{position:absolute;left:45px;width:1110px;height:858px;background:var(--paper);box-shadow:0 6px 24px rgba(0,0,0,.15);overflow:hidden}
.spread--outside{top:240px}
.spread--inside{top:1302px}
.panel{position:absolute;top:0;width:370px;height:858px;overflow:hidden}
.panel--1{left:0}.panel--2{left:370px}.panel--3{left:740px}
.panel + .panel{border-left:1px solid rgba(0,0,0,.05)}
.shape{position:absolute;left:0;top:0}
.brand{position:absolute;font-family:"Oswald",Arial,sans-serif;font-weight:600;color:var(--navy);display:flex;align-items:center;gap:8px;line-height:1}
.brand__dot{width:12px;height:12px;border-radius:50%;background:var(--gold);display:inline-block}
.heading{font-family:"Oswald",Arial,sans-serif;font-weight:700;color:var(--navy);text-transform:uppercase;letter-spacing:.5px}
.body-copy{font-size:10.5px;line-height:1.55;color:var(--ink)}
.body-copy p + p{margin-top:9px}

/* outside – inner flap */
.definition{position:absolute;left:30px;top:104px;width:310px}
.definition__term{font-size:11px;font-weight:700;letter-spacing:1px;color:var(--navy)}
.definition__meaning{font-style:italic;font-weight:700;font-size:14px;color:var(--navy);margin-top:6px}
.definition__usage{font-style:italic;font-size:10px;margin-top:4px}
.tab{position:absolute;left:0;height:22px;padding:0 16px 0 30px;background:var(--navy);color:#fff;font-family:"Oswald",Arial,sans-serif;font-size:12px;letter-spacing:1px;display:flex;align-items:center}
.tab--who{top:196px}
.who-copy{position:absolute;left:30px;top:234px;width:310px}

/* outside – back panel */
.back__logo{left:0;right:0;top:70px;justify-content:center;font-size:34px;color:#fff}
.contact-label{position:absolute;left:50%;top:136px;transform:translateX(-50%);border:1.5px solid var(--gold);color:var(--gold);font-family:"Oswald",Arial,sans-serif;font-size:14px;letter-spacing:2px;padding:3px 18px}
.offices{position:absolute;left:34px;top:190px;width:310px;display:grid;grid-template-columns:1fr 1fr;column-gap:20px;color:#fff}
.state{font-family:"Oswald",Arial,sans-serif;font-size:14px;color:var(--yellow);letter-spacing:1px;margin:10px 0 4px}
.office{display:flex;gap:6px;font-size:10px;line-height:1.35;margin-bottom:6px}
.office svg{flex:none;margin-top:2px}
.office span{display:block;opacity:.85}
.back-details{position:absolute;right:36px;top:660px;text-align:right;font-size:11.5px;line-height:2;color:var(--ink)}
.back-details div{display:flex;justify-content:flex-end;align-items:center;gap:8px}
.icon-dot{width:12px;height:12px;border-radius:50%;background:var(--red);display:inline-block}

/* outside – cover */
.cover__logo{right:38px;top:56px;font-size:36px}
.cover__title{position:absolute;left:88px;top:600px;font-size:44px;line-height:1.02}
.cover__web{position:absolute;left:88px;top:770px;font-size:14px;color:var(--red);display:flex;align-items:center;gap:8px}

/* inside – what we do */
.what__title{position:absolute;left:28px;top:330px;font-size:26px}
.what-copy{position:absolute;left:28px;top:378px;width:318px}

/* inside – staffing options */
.options__title{position:absolute;left:0;right:0;top:262px;text-align:center;color:#fff;font-size:26px}
.option{position:absolute;left:30px;width:318px;display:flex;gap:14px}
.option__icon{flex:none;width:40px;height:40px;border-radius:50%;background:var(--yellow);display:flex;align-items:center;justify-content:center}
.option__name{font-family:"Oswald",Arial,sans-serif;font-size:13px;color:var(--yellow);letter-spacing:1px}
.option__text{font-size:10px;line-height:1.5;color:#fff;margin-top:3px}
.option--temp{top:330px}.option--temp-hire{top:480px}.option--direct{top:630px}

/* inside – onsite management */
.onsite__title{position:absolute;left:28px;top:40px;font-size:22px}
.onsite-copy{position:absolute;left:28px;top:78px;width:318px}
.sector{position:absolute;left:0;width:370px}
.sector__bar{height:20px;width:190px;padding-left:28px;color:#fff;font-family:"Oswald",Arial,sans-serif;font-size:12px;letter-spacing:1px;display:flex;align-items:center;clip-path:polygon(0 0,100% 0,92% 100%,0 100%)}
.sector--light .sector__bar{background:var(--red)}
.sector--trades .sector__bar{background:var(--green)}
.sector--office .sector__bar{background:var(--yellow);color:var(--navy)}
.sector ul{display:grid;grid-template-columns:1fr 1fr;column-gap:10px;list-style:none;padding:8px 28px 0 40px;font-size:10.5px;line-height:1.6}
.sector li::before{content:"•";color:var(--navy);margin-right:6px}
.sector--light{top:210px}.sector--trades{top:318px}.sector--office{top:426px}
</style>
</head>
<body>

<!-- OUTSIDE SPREAD -->
<section class="spread spread--outside" aria-label="Brochure outside">

  <!-- inner flap -->
  <article class="panel panel--1">
    <div class="brand" style="left:30px;top:40px;font-size:30px">Tarn Workforce<span class="brand__dot"></span></div>
    <div class="definition">
      <div class="definition__term">DEFINITION OF TARN – VERB</div>
      <div class="definition__meaning">To be in harmony or accord; fit; agree.</div>
      <div class="definition__usage">The candidate skills and the job requirements tarn well together.</div>
    </div>
    <div class="tab tab--who">WHO WE ARE</div>
    <div class="who-copy body-copy">
      <p>At Tarn Workforce, we are passionate about our mission: to help great companies find great people and to help great people find careers that fit the way they live and work.</p>
      <p>We partner with logistics, distribution and manufacturing firms of every size, building teams that are reliable, skilled and ready to grow with our clients.</p>
      <p>Tarn is a values-based organization. Every placement is guided by respect, honesty and a real effort to match the right person with the right role.</p>
    </div>
    <svg class="shape" width="370" height="858" viewBox="0 0 370 858" aria-hidden="true">
      <polygon points="0,600 370,520 370,540 0,620" fill="var(--navy)"/>
      <polygon points="0,858 0,640 90,620 0,760" fill="var(--navy)" opacity=".9"/>
    </svg>
    <svg class="shape" width="370" height="858" viewBox="0 0 370 858" role="img" aria-label="Photo of a team planning work at a desk with laptops and notes">
      <defs><linearGradient id="photoDesk" x1="0" y1="0" x2="1" y2="1"><stop offset="0" stop-color="#8a7a6c"/><stop offset="1" stop-color="#c9b9a4"/></linearGradient></defs>
      <polygon points="0,620 370,540 370,858 0,858" fill="url(#photoDesk)"/>
      <polygon points="0,858 0,700 120,858" fill="var(--navy)"/>
    </svg>
  </article>

  <!-- back panel -->
  <article class="panel panel--2">
    <svg class="shape" width="370" height="858" viewBox="0 0 370 858" aria-hidden="true">
      <path d="M0 0H370V520Q200 600 0 560Z" fill="var(--navy)"/>
      <path d="M0 560Q200 600 370 520V534Q200 614 0 574Z" fill="var(--gold)"/>
    </svg>
    <div class="brand back__logo">Tarn Workforce</div>
    <div class="contact-label">CONTACT US</div>
    <div class="offices">
      <div>
        <div class="state">GEORGIA</div>
        <div class="office"><svg width="9" height="12" viewBox="0 0 9 12"><path d="M4.5 0A4.5 4.5 0 0 0 0 4.5C0 8 4.5 12 4.5 12S9 8 9 4.5A4.5 4.5 0 0 0 4.5 0Z" fill="var(--yellow)"/></svg><div>Millbrook<span>555-014-2290</span></div></div>
        <div class="office"><svg width="9" height="12" viewBox="0 0 9 12"><path d="M4.5 0A4.5 4.5 0 0 0 0 4.5C0 8 4.5 12 4.5 12S9 8 9 4.5A4.5 4.5 0 0 0 4.5 0Z" fill="var(--yellow)"/></svg><div>Fernhollow<span>555-014-3371</span></div></div>
        <div class="office"><svg width="9" height="12" viewBox="0 0 9 12"><path d="M4.5 0A4.5 4.5 0 0 0 0 4.5C0 8 4.5 12 4.5 12S9 8 9 4.5A4.5 4.5 0 0 0 4.5 0Z" fill="var(--yellow)"/></svg><div>Harbor Reach<span>555-014-5682</span></div></div>
        <div class="office"><svg width="9" height="12" viewBox="0 0 9 12"><path d="M4.5 0A4.5 4.5 0 0 0 0 4.5C0 8 4.5 12 4.5 12S9 8 9 4.5A4.5 4.5 0 0 0 4.5 0Z" fill="var(--yellow)"/></svg><div>Cedar Glen<span>555-014-7045</span></div></div>
        <div class="state">TEXAS</div>
        <div class="office"><svg width="9" height="12" viewBox="0 0 9 12"><path d="M4.5 0A4.5 4.5 0 0 0 0 4.5C0 8 4.5 12 4.5 12S9 8 9 4.5A4.5 4.5 0 0 0 4.5 0Z" fill="var(--yellow)"/></svg><div>Redmesa<span>555-014-8123</span></div></div>
      </div>
      <div>
        <div class="state">INDIANA</div>
        <div class="office"><svg width="9" height="12" viewBox="0 0 9 12"><path d="M4.5 0A4.5 4.5 0 0 0 0 4.5C0 8 4.5 12 4.5 12S9 8 9 4.5A4.5 4.5 0 0 0 4.5 0Z" fill="var(--yellow)"/></svg><div>Westmere<span>555-014-9264</span></div></div>
        <div class="state">PENNSYLVANIA</div>
        <div class="office"><svg width="9" height="12" viewBox="0 0 9 12"><path d="M4.5 0A4.5 4.5 0 0 0 0 4.5C0 8 4.5 12 4.5 12S9 8 9 4.5A4.5 4.5 0 0 0 4.5 0Z" fill="var(--yellow)"/></svg><div>Stonebridge<span>555-014-1187</span></div></div>
        <div class="office"><svg width="9" height="12" viewBox="0 0 9 12"><path d="M4.5 0A4.5 4.5 0 0 0 0 4.5C0 8 4.5 12 4.5 12S9 8 9 4.5A4.5 4.5 0 0 0 4.5 0Z" fill="var(--yellow)"/></svg><div>Lindenvale<span>555-014-6630</span></div></div>
      </div>
    </div>
    <div class="back-details">
      <div>555-014-2290 Office <span class="icon-dot"></span></div>
      <div>www.TarnWorkforce-example.com <span class="icon-dot"></span></div>
      <div>482 Alder Lane <span class="icon-dot"></span></div>
      <div>Suite 210, Millbrook, GA 30000</div>
    </div>
  </article>

  <!-- cover -->
  <article class="panel panel--3">
    <div class="brand cover__logo">Tarn Workforce<span class="brand__dot"></span></div>
    <svg class="shape" width="370" height="858" viewBox="0 0 370 858" role="img" aria-label="Photo of three diverse colleagues reviewing a brochure together in an office">
      <defs><linearGradient id="photoCover" x1="0" y1="0" x2="1" y2="1"><stop offset="0" stop-color="#d9d3cc"/><stop offset=".55" stop-color="#b98e4a"/><stop offset="1" stop-color="#6d5a55"/></linearGradient></defs>
      <polygon points="0,150 370,150 370,500 0,560" fill="url(#photoCover)"/>
    </svg>
    <svg class="shape" width="370" height="858" viewBox="0 0 370 858" aria-hidden="true">
      <polygon points="370,300 370,520 190,540" fill="var(--navy)"/>
      <polygon points="0,545 370,490 370,510 0,580" fill="var(--gold)"/>
      <polygon points="0,858 0,820 40,858" fill="var(--navy)"/>
    </svg>
    <h1 class="heading cover__title">Attaining<br>Client<br>Objectives</h1>
    <div class="cover__web"><span class="icon-dot"></span>www.TarnWorkforce-example.com</div>
  </article>
</section>

<!-- INSIDE SPREAD -->
<section class="spread spread--inside" aria-label="Brochure inside">

  <!-- what we do -->
  <article class="panel panel--1">
    <svg class="shape" width="370" height="858" viewBox="0 0 370 858" role="img" aria-label="Photo of two coworkers smiling in a busy production kitchen">
      <defs><linearGradient id="photoKitchen" x1="0" y1="0" x2="1" y2="1"><stop offset="0" stop-color="#4a4440"/><stop offset="1" stop-color="#9a8f86"/></linearGradient></defs>
      <polygon points="0,0 370,0 370,210 260,300 170,240 0,290" fill="url(#photoKitchen)"/>
    </svg>
    <svg class="shape" width="370" height="858" viewBox="0 0 370 858" aria-hidden="true">
      <polyline points="0,290 170,240 260,300 370,210" fill="none" stroke="var(--gold)" stroke-width="8"/>
      <polygon points="0,858 0,800 60,858" fill="var(--navy)"/>
    </svg>
    <h2 class="heading what__title">What We Do</h2>
    <div class="what-copy body-copy">
      <p>At Tarn Workforce we do things a little differently. We don't just fill orders; we build teams. Our recruiters take time to learn your operation, your culture and your goals so every candidate we send is ready to contribute from the first shift.</p>
      <p>We believe in growing our partners with people who care. Every applicant is screened, interviewed and reference checked, including background and drug checks when required by the client.</p>
      <p>Tarn Workforce is powered by a recruiting engine that never stops. With a deep bench of qualified talent across warehouse, production, office and skilled roles, we respond fast when demand changes and keep your lines moving through peak seasons.</p>
      <p>At Tarn Workforce we have a great opportunity to positively impact the lives of employees and job seekers. We treat that as a privilege and a responsibility we take seriously every day.</p>
      <p>We look forward to learning about your specific needs and showing how Tarn can bring immediate and lasting value.</p>
    </div>
  </article>

  <!-- staffing options -->
  <article class="panel panel--2">
    <svg class="shape" width="370" height="858" viewBox="0 0 370 858" aria-hidden="true">
      <rect width="370" height="858" fill="var(--navy)"/>
      <polygon points="0,0 370,0 370,120 0,200" fill="var(--navy-deep)"/>
      <circle cx="185" cy="160" r="74" fill="none" stroke="var(--gold)" stroke-width="6"/>
    </svg>
    <svg class="shape" width="370" height="858" viewBox="0 0 370 858" role="img" aria-label="Round photo of a warehouse worker in safety gear">
      <defs><linearGradient id="photoWorker" x1="0" y1="0" x2="0" y2="1"><stop offset="0" stop-color="#8c8f96"/><stop offset="1" stop-color="#d98a2b"/></linearGradient></defs>
      <circle cx="185" cy="160" r="68" fill="url(#photoWorker)"/>
    </svg>
    <h2 class="heading options__title">Staffing Options</h2>
    <div class="option option--temp">
      <div class="option__icon"><svg width="20" height="20" viewBox="0 0 20 20"><circle cx="10" cy="10" r="8" fill="none" stroke="var(--navy)" stroke-width="2"/><path d="M10 5V10L13 12" fill="none" stroke="var(--navy)" stroke-width="2"/></svg></div>
      <div><div class="option__name">TEMPORARY</div><p class="option__text">Flexible workers when you need them. Cover peaks, projects and absences while we handle payroll, taxes and insurance so your team stays focused on results.</p></div>
    </div>
    <div class="option option--temp-hire">
      <div class="option__icon"><svg width="20" height="20" viewBox="0 0 20 20"><path d="M3 10H15M11 6L15 10L11 14" fill="none" stroke="var(--navy)" stroke-width="2"/></svg></div>
      <div><div class="option__name">TEMP TO HIRE</div><p class="option__text">Evaluate skills, attitude and fit on the job before making a commitment. When the match is right, convert the associate to your own payroll with ease.</p></div>
    </div>
    <div class="option option--direct">
      <div class="option__icon"><svg width="20" height="20" viewBox="0 0 20 20"><path d="M4 10L8 14L16 6" fill="none" stroke="var(--navy)" stroke-width="2.4"/></svg></div>
      <div><div class="option__name">DIRECT HIRE</div><p class="option__text">We source, screen and present top candidates for permanent roles, saving you time and cost while delivering people who are ready to grow with your company.</p></div>
    </div>
  </article>

  <!-- onsite management -->
  <article class="panel panel--3">
    <h2 class="heading onsite__title">Onsite Management</h2>
    <div class="onsite-copy body-copy">
      <p>Tarn Workforce offers dedicated onsite coordinators for clients with large or changing teams. We manage attendance, training, safety and daily scheduling so your supervisors can focus on production and quality goals.</p>
    </div>
    <div class="sector sector--light">
      <div class="sector__bar">LIGHT INDUSTRIAL</div>
      <ul><li>Manufacturing</li><li>Packaging</li><li>Logistics</li><li>Food Production</li><li>Assembly</li><li>Hospitality</li></ul>
    </div>
    <div class="sector sector--trades">
      <div class="sector__bar">SKILLED TRADES</div>
      <ul><li>Electrical</li><li>CNC Operators</li><li>Maintenance</li><li>Machine Operators</li><li>Welding</li><li>Plumbing</li></ul>
    </div>
    <div class="sector sector--office">
      <div class="sector__bar">OFFICE/CLERICAL</div>
      <ul><li>Accounting</li><li>Data Entry</li><li>Administrative</li><li>Executive Support</li><li>Call Center</li><li>Legal</li><li>Customer Service</li><li>Sales</li></ul>
    </div>
    <svg class="shape" width="370" height="858" viewBox="0 0 370 858" role="img" aria-label="Photo of two workers checking boxes in a distribution warehouse">
      <defs><linearGradient id="photoWarehouse" x1="0" y1="0" x2="1" y2="1"><stop offset="0" stop-color="#b7a58c"/><stop offset="1" stop-color="#5e6c86"/></linearGradient></defs>
      <polygon points="0,620 370,560 370,858 0,858" fill="url(#photoWarehouse)"/>
    </svg>
    <svg class="shape" width="370" height="858" viewBox="0 0 370 858" aria-hidden="true">
      <polygon points="0,615 370,555 370,545 0,605" fill="var(--gold)"/>
      <polygon points="370,545 370,620 300,556" fill="var(--navy)"/>
      <polygon points="0,620 0,858 120,858" fill="var(--navy)"/>
    </svg>
  </article>
</section>

</body>
</html>
```